Recto Verso Audiology Business Card

Business card with a beautiful design on the back. On the Recto you need the following data Lindqvist Oren Audiologist Hearing Solutions Hearing Protection Tinnitus Hyperacusis Tel: 0482/37 59 08 Email: On the back, you need something nice like the attached file. The logo "Corra Luna" can be in the center The colors of the Logo can not be changed If possible stay in the same colors as the logo Another solution is to put the logo on the front and have a nice back (A mosaic of small ears, hearing aids or other ..) Thank you _______________________________________________________________ Visit card On the Recto Lindqvist Oren Audiologist Hearing Solutions Hearing Protection Tinnitus Hyperacusis Tel: 0482/37 59 08 Email: You can put the logo " Corra Luna "on the Recto of the Verso The colors of the logo can not be changed. If you put the logo on the back, it must be well integrated. On the Verso I need something in the files. something stylish. It's a visit card for an audiologist. You can get ears of hearing aids if you need. Thanks

Target Market(s)

customers

Contact Information for Business Card

Carte de visite standard ou A6

Font styles to use
Serif
Sans Serif

Colors
33a6d7

Requirements
Must have
• the logo and a stylized background.
Nice to have
• It would be nice to have a back side related to audiology (ears, hearing aids etc.)

```html
<!DOCTYPE html>
<html lang="en">
<head>
<meta charset="utf-8">
<title>Corra Luna – Audiology Business Card</title>
<link rel="stylesheet" href="https://fonts.googleapis.com/css2?family=Roboto:wght@400;500&family=Roboto+Condensed:wght@500&display=swap">
<style>
  :root {
    --stage: #e9e7e4;
    --card-back: #26292b;
    --card-front: #2a2a2b;
    --pattern-tone: #2f4448;
    --brand: #33a6d7;
    --brand-soft: #4bc3d3;
    --title-grey: #5a6570;
    --text-light: #eef0f2;
    --rule: #cfd3d6;
  }
  * { margin: 0; padding: 0; box-sizing: border-box; }
  html, body { width: 1200px; height: 419px; overflow: hidden; }
  body {
    background: var(--stage);
    font-family: "Roboto", Arial, sans-serif;
    display: flex;
    align-items: center;
    justify-content: center;
    gap: 70px;
  }
  .card {
    position: relative;
    width: 460px;
    height: 270px;
    border-radius: 3px;
    box-shadow: 0 8px 22px rgba(0,0,0,.25);
    overflow: hidden;
  }
  /* Verso */
  .card--verso { background: var(--card-back); }
  .ear-pattern {
    position: absolute;
    inset: 0;
    background: radial-gradient(circle at 50% 50%, var(--pattern-tone), var(--card-back) 85%);
  }
  .brand-block {
    position: absolute;
    left: 50%;
    top: 50%;
    transform: translate(-50%, -50%);
    display: flex;
    align-items: center;
    gap: 10px;
    padding: 14px 18px;
    background: var(--card-back);
  }
  .brand-mark {
    width: 12px; height: 12px;
    background: var(--brand);
  }
  .brand-name {
    font-family: "Roboto", Arial, sans-serif;
    font-weight: 500;
    font-size: 26px;
    letter-spacing: 1px;
    text-transform: uppercase;
    color: var(--brand-soft);
  }
  /* Recto */
  .card--recto { background: var(--card-front); }
  .card--recto .brand-block {
    left: auto; top: 70px; right: 34px;
    transform: none;
    padding: 0;
    background: none;
  }
  .card--recto .brand-name { font-size: 20px; }
  .holder {
    position: absolute;
    left: 42px;
    top: 118px;
  }
  .holder-name {
    font-family: "Roboto Condensed", Arial, sans-serif;
    font-weight: 500;
    font-size: 20px;
    letter-spacing: .5px;
    text-transform: uppercase;
    color: var(--brand-soft);
    line-height: 1.1;
  }
  .holder-title {
    font-size: 14px;
    color: var(--title-grey);
  }
  .divider {
    position: absolute;
    left: 42px;
    right: 42px;
    top: 162px;
    height: 1px;
    background: var(--rule);
  }
  .contacts {
    position: absolute;
    left: 42px;
    top: 172px;
    list-style: none;
  }
  .contacts li {
    display: flex;
    align-items: center;
    gap: 8px;
    font-size: 13px;
    color: var(--text-light);
    line-height: 20px;
  }
  .contacts svg { width: 11px; height: 11px; fill: var(--brand-soft); }
  .services {
    position: absolute;
    right: 34px;
    bottom: 26px;
    text-align: right;
    font-size: 13px;
    line-height: 17px;
    color: var(--text-light);
  }
</style>
</head>
<body>
  <section class="card card--verso">
    <div class="ear-pattern" role="img" aria-label="Repeating pattern of small stylised ears with sound waves"></div>
    <div class="brand-block">
      <span class="brand-mark"></span>
      <span class="brand-name">Corra Luna</span>
    </div>
  </section>

  <section class="card card--recto">
    <div class="brand-block">
      <span class="brand-mark"></span>
      <span class="brand-name">Corra Luna</span>
    </div>

    <div class="holder">
      <p class="holder-name">Lindqvist Oren</p>
      <p class="holder-title">Audiologist Hearing</p>
    </div>

    <div class="divider"></div>

    <ul class="contacts">
      <li>
        <svg viewBox="0 0 24 24" aria-hidden="true"><path d="M6.6 10.8a15.1 15.1 0 0 0 6.6 6.6l2.2-2.2a1 1 0 0 1 1-.25 11.4 11.4 0 0 0 3.6.57 1 1 0 0 1 1 1V20a1 1 0 0 1-1 1A17 17 0 0 1 3 4a1 1 0 0 1 1-1h3.5a1 1 0 0 1 1 1c0 1.25.2 2.45.57 3.57a1 1 0 0 1-.25 1z"/></svg>
        0482/37 59 08
      </li>
      <li>
        <svg viewBox="0 0 24 24" aria-hidden="true"><path d="M2 5h20v14H2z M2 5l10 8 10-8" fill="none" stroke="currentColor"/><path d="M2 5h20v2l-10 7L2 7z"/><path d="M2 8l10 7 10-7v11H2z"/></svg>
        info@corraluna.com
      </li>
      <li>
        <svg viewBox="0 0 24 24" aria-hidden="true"><circle cx="12" cy="12" r="10"/></svg>
        www.corraluna.com
      </li>
    </ul>

    <div class="services">
      <p>Solutions Hearing</p>
      <p>Protection</p>
      <p>Tinnitus | Hyperacusis</p>
    </div>
  </section>
</body>
</html>
```